Marwick Law Letterhead

We need a new letterhead design for a Law Firm. The address for the law firm is 1475 Calloway Street, Suite 210, Houston, Texas 77041. Phone Number: 832-361-9027; Fax Number: 832-614-7359. The logo is uploaded to the project.

```html
<!DOCTYPE html>
<html lang="en">
<head>
<meta charset="utf-8">
<title>Marwick Law Letterhead</title>
<link rel="stylesheet" href="https://fonts.googleapis.com/css2?family=Figtree:wght@400;500&family=Cormorant+Garamond:wght@600&display=swap">
<style>
  :root {
    --navy: #1d3160;
    --red: #c4151f;
    --ink: #2b2b2b;
    --paper: #ffffff;
    --backdrop: #e8e8e8;
    --signature-tone: #d9d9d9;
  }
  html, body {
    margin: 0;
    width: 1154px;
    height: 1200px;
    overflow: hidden;
    background: var(--backdrop);
  }
  .letterhead {
    position: absolute;
    left: 148px;
    top: 0;
    width: 1066px;
    height: 1490px;
    background: var(--paper);
    transform: scale(0.8054);
    transform-origin: top left;
    font-family: "Figtree", "Helvetica Neue", Arial, sans-serif;
    color: var(--ink);
  }
  .brand {
    position: absolute;
    left: 41px;
    top: 96px;
    display: flex;
    align-items: center;
    gap: 18px;
  }
  .brand-square {
    width: 76px;
    height: 88px;
    background: var(--navy);
  }
  .brand-text { display: flex; flex-direction: column; }
  .brand-name {
    font-family: "Cormorant Garamond", Georgia, serif;
    font-weight: 600;
    font-size: 50px;
    line-height: 1;
    color: var(--navy);
    letter-spacing: 0.5px;
  }
  .brand-tagline {
    margin-top: 12px;
    font-family: "Cormorant Garamond", Georgia, serif;
    font-weight: 600;
    font-size: 10px;
    letter-spacing: 1.6px;
    text-transform: uppercase;
    color: var(--navy);
  }
  .header-rule {
    position: absolute;
    left: 38px;
    top: 238px;
    width: 988px;
    height: 4px;
    background: var(--navy);
  }
  .recipient {
    position: absolute;
    left: 39px;
    top: 331px;
    font-size: 18.5px;
    line-height: 26.6px;
    letter-spacing: 0.3px;
    font-style: normal;
  }
  .body {
    position: absolute;
    left: 42px;
    top: 444px;
    width: 987px;
    font-size: 18.5px;
    line-height: 26.6px;
    letter-spacing: 0.45px;
    text-align: justify;
    hyphens: auto;
    -webkit-hyphens: auto;
    color: #333;
  }
  .body p { margin: 0 0 26.6px; }
  .closing {
    position: absolute;
    left: 39px;
    top: 1075px;
    font-size: 22px;
    letter-spacing: 0.3px;
    color: #1f1f1f;
  }
  .signature {
    position: absolute;
    left: 37px;
    top: 1112px;
    width: 120px;
    height: 36px;
    background: var(--signature-tone);
    border-radius: 3px;
  }
  .footer-line {
    position: absolute;
    left: 0;
    width: 100%;
    background: var(--red);
  }
  .footer-line.top { top: 1356px; height: 4px; }
  .footer-line.bottom { top: 1448px; height: 5px; }
  .footer-band {
    position: absolute;
    left: 0;
    top: 1364px;
    width: 100%;
    height: 80px;
    background: var(--navy);
    display: flex;
    align-items: center;
    justify-content: center;
    gap: 18px;
    color: #fff;
    font-size: 19.5px;
    letter-spacing: 0.2px;
  }
  .contact { display: flex; align-items: center; gap: 12px; }
  .contact svg { width: 20px; height: 20px; }
</style>
</head>
<body>
  <main class="letterhead">
    <div class="brand">
      <div class="brand-square"></div>
      <div class="brand-text">
        <div class="brand-name">Marwick Law</div>
        <div class="brand-tagline">Standing firmly beside every client</div>
      </div>
    </div>
    <div class="header-rule"></div>

    <address class="recipient">
      Mr/s<br>First Name and Last Name<br>Company Name<br>Address
    </address>

    <section class="body">
      <p>Lorem ipsum dolor sit amet,consectetur adipiscing sed do eiusmod tempor incididunt laboreet dolore magna aliqua.Ut enim ad minim.veniam, quis nostrud exercitation ullamco laboris nisi ut aliquip exea commodo consequat.Lorem ipsum dolor sit amet,consectetur adipiscing sed do eiusmod tempor incididunt.labore et dolore magna aliqua. Ut enim</p>
      <p>Lorem ipsum dolor sit amet, consectetur adipiscing sed do eiusmod tempor incididunt labore et dolore magna aliqua. Ut enim ad minim veniam, quis nostrud exercitation ullamco laboris nisi ut aliquip exea commodo consequat.Duis aute irure dolor in reprehenderit in voluptate velit esse cillum irure dolor in reprehenderit in voluptate velit esse irure</p>
      <p>Lorem ipsum dolor sit amet, consectetur adipiscing sed do eiusmod tempor incididunt labore et dolore magna aliqua. consequat. Duis aute irure dolor in.reprehenderit in voluptate velit esse cillum dolore eu fugiat nulla pariatur. Excepteur sint occaecat cupidatat non proident, sunt in culpa qui officia deserunt mollit,</p>
      <p>Lorem ipsum dolor sit amet, consectetur adipiscing sed do eiusmod tempor incididunt labore et dolore magna aliqua. Ut enim Lorem ipsum dolor sit amet, consectetur adipiscing sed do eiusmod tempor incididunt labore et dolore magna aliqua. Ut enim Lorem ipsum aliqua.ipsum</p>
      <p>Lorem ipsum dolor sit amet, consectetur adipiscing sed do eiusmod tempor incididunt labore et dolore magna aliqua. Ut enim ad minim veniam, quis nostrud exercitation ullamco laboris nisi ut aliquip exea commodo consequat.Duis aute irure dolor in reprehenderit in voluptate velit esse cillum irure dolor in reprehenderit in voluptate velit esse irure</p>
    </section>

    <div class="closing">Regards</div>
    <div class="signature" role="img" aria-label="Handwritten signature"></div>

    <div class="footer-line top"></div>
    <footer class="footer-band">
      <span class="address">1475 Calloway Street, Suite 210, Houston, Texas 77041</span>
      <span class="contact">
        <svg viewBox="0 0 24 24" aria-hidden="true"><path fill="#fff" d="M6.6 10.8a15.1 15.1 0 0 0 6.6 6.6l2.2-2.2c.3-.3.7-.4 1-.2 1.1.4 2.3.6 3.6.6.6 0 1 .4 1 1V20c0 .6-.4 1-1 1A17 17 0 0 1 3 4c0-.6.4-1 1-1h3.5c.6 0 1 .4 1 1 0 1.3.2 2.5.6 3.6.1.3 0 .7-.2 1z"/></svg>
        832-361-9027
      </span>
      <span class="contact">
        <svg viewBox="0 0 24 24" aria-hidden="true"><path fill="#fff" d="M7 3h10v5H7zM4 9h16a2 2 0 0 1 2 2v6h-4v4H6v-4H2v-6a2 2 0 0 1 2-2zm4 7v3h8v-3z"/></svg>
        832-614-7359
      </span>
    </footer>
    <div class="footer-line bottom"></div>
  </main>
</body>
</html>
```